Lendquay wedsite and logo refresh

We are looking for someone to refresh the look and feel of Lendquay.co.nz we are moving it towards a more traditional brokerage.

Target Market(s)

30 to 55 year old professionals

Coding

Coded - Design and coding required

Number of Pages Required

3 page

Requirements
Nice to have
• we are needing a modern professional look

```html
<!DOCTYPE html>
<html lang="en">
<head>
<meta charset="utf-8">
<title>Lendquay – Find and Compare Rates</title>
<link href="https://fonts.googleapis.com/css2?family=Montserrat:wght@500;600;700;800&family=Roboto:wght@300;400;500&display=swap" rel="stylesheet">
<style>
:root{
  --orange:#f15a24;
  --black:#111111;
  --ink:#1d1d1d;
  --grey:#666666;
  --white:#ffffff;
  --plum:#6f5a6b;
  --mustard:#f4bf1f;
  --forest:#33734f;
  --teal:#00b5be;
  --lilac:#b5afc4;
  --lime:#a8cb55;
}
*{box-sizing:border-box;margin:0;padding:0}
html,body{width:1200px;height:2817px;overflow:hidden;background:var(--white)}
body{position:relative;font-family:'Roboto',sans-serif;color:var(--ink)}
.abs{position:absolute}

/* header */
.site-header{position:absolute;left:0;top:0;width:1200px;height:66px;background:var(--orange);z-index:5}
.brand{position:absolute;left:90px;top:16px;font-family:'Montserrat',sans-serif;font-weight:600;font-size:30px;letter-spacing:1px;color:var(--white);line-height:34px}
.nav a{position:absolute;top:24px;font-size:16px;font-weight:500;color:var(--white);text-decoration:none;letter-spacing:.3px}
.nav a.active{color:var(--black)}
.pill{position:absolute;top:12px;height:41px;border-radius:21px;background:var(--white);color:var(--orange);font-size:16px;font-weight:500;display:flex;align-items:center;justify-content:center}
.lang{position:absolute;left:1003px;top:13px;width:40px;height:40px}
.lang-label{position:absolute;left:1055px;top:25px;color:var(--white);font-size:16px;font-weight:500}
.menu-box{position:absolute;left:1110px;top:0;width:90px;height:66px;background:var(--black)}

/* hero */
.hero-photo{position:absolute;left:0;top:66px;width:1200px;height:600px;background:linear-gradient(100deg,#5a4438 0%,#8a6a58 25%,#b9b2aa 50%,#d8d3cd 65%,#7a5a45 85%,#c9c2ba 100%)}
.hero-title{position:absolute;left:86px;top:210px;font-family:'Montserrat',sans-serif;font-weight:800;font-size:55px;line-height:58px;color:var(--white)}
.btn{position:absolute;background:var(--orange);color:var(--white);border-radius:26px;font-size:17px;font-weight:500;display:flex;align-items:center;justify-content:center;letter-spacing:.3px}

/* compare */
.section-title{position:absolute;left:0;width:1200px;text-align:center;font-family:'Montserrat',sans-serif;font-weight:700;font-size:42px;color:var(--black)}
.lead{position:absolute;left:0;width:1200px;text-align:center;font-size:16px;line-height:26px;color:var(--ink)}
.cards-bg{position:absolute;left:0;top:960px;width:1200px;height:679px;background:linear-gradient(120deg,#2d2a2a 0%,#4a4442 40%,#6a6360 60%,#3a3533 100%)}
.card{position:absolute;width:246px;height:186px;background:var(--white)}
.card .tile{position:absolute;left:8px;top:0;width:230px;height:116px;display:flex;align-items:center;justify-content:center}
.card .name{position:absolute;left:0;width:246px;text-align:center;font-family:'Montserrat',sans-serif;font-weight:500;font-size:20px;line-height:22px;color:var(--ink)}
.card .soon{position:absolute;left:0;top:172px;width:246px;text-align:center;font-size:11px;color:#777}
.card .name.one{top:138px}
.card .name.two{top:135px;font-size:19px}
.card .name.mid{top:127px;font-size:19px}

/* why */
.why-photo{position:absolute;left:405px;top:1852px;width:390px;height:390px;border-radius:50%;background:radial-gradient(circle at 50% 40%,#d9b98a 0%,#b48f60 45%,#5a4a3a 100%)}
.feature{position:absolute;width:290px}
.feature.right{text-align:right}
.feature h3{font-size:18px;font-weight:500;color:var(--black);margin-top:0}
.feature p{font-size:14px;font-weight:300;line-height:26px;color:var(--grey);margin-top:12px}

/* footer */
.site-footer{position:absolute;left:0;top:2437px;width:1200px;height:380px;background:var(--orange);color:var(--white)}
.footer-brand{position:absolute;left:90px;top:77px;font-family:'Montserrat',sans-serif;font-weight:600;font-size:30px;letter-spacing:1px}
.col-head{position:absolute;top:82px;font-size:17px;font-weight:500;letter-spacing:.4px}
.col-list{position:absolute;top:122px;font-size:14px;line-height:26px;list-style:none}
.news-input{position:absolute;left:762px;top:128px;width:349px;height:39px;background:var(--white);color:#777;font-size:15px;padding:10px 16px}
.news-btn{position:absolute;left:762px;top:176px;width:349px;height:38px;background:var(--black);color:var(--white);font-size:16px;font-weight:500;display:flex;align-items:center;justify-content:center}
.copyright{position:absolute;left:0;top:336px;width:1200px;text-align:center;font-size:12px}
</style>
</head>
<body>

<header class="site-header">
  <div class="brand">LENDQUAY</div>
  <nav class="nav">
    <a class="active" style="left:328px">SERVICES</a>
    <a style="left:452px">ABOUT</a>
    <a style="left:553px">CONTACT</a>
  </nav>
  <div class="pill" style="left:675px;width:109px">LOG IN</div>
  <div class="pill" style="left:792px;width:190px">SIGN UP FOR FREE</div>
  <svg class="lang" viewBox="0 0 40 40" aria-hidden="true">
    <defs><clipPath id="flagclip"><circle cx="20" cy="20" r="19"/></clipPath></defs>
    <g clip-path="url(#flagclip)">
      <rect width="40" height="40" fill="#23357a"/>
      <path d="M0 0L40 40M40 0L0 40" stroke="#fff" stroke-width="8"/>
      <path d="M0 0L40 40M40 0L0 40" stroke="#c8102e" stroke-width="3"/>
      <path d="M20 0V40M0 20H40" stroke="#fff" stroke-width="11"/>
      <path d="M20 0V40M0 20H40" stroke="#c8102e" stroke-width="6"/>
    </g>
  </svg>
  <div class="lang-label">EN <svg width="10" height="8" viewBox="0 0 10 8"><path d="M1 2l4 4 4-4" stroke="#fff" stroke-width="1.6" fill="none"/></svg></div>
  <div class="menu-box">
    <svg class="abs" style="left:36px;top:26px" width="18" height="14" viewBox="0 0 18 14"><path d="M0 1.5H18M0 7H18M0 12.5H18" stroke="#fff" stroke-width="3"/></svg>
  </div>
</header>

<section class="hero">
  <div class="hero-photo" role="img" aria-label="Woman working on a laptop at a kitchen bench with a brick wall behind"></div>
  <h1 class="hero-title">NO OBLIGATIONS<br>NO FEES<br>NO WORRIES</h1>
  <div class="btn" style="left:90px;top:421px;width:279px;height:52px">FIND AND COMPARE RATES</div>
  <svg class="abs" style="left:0;top:600px" width="1200" height="90" viewBox="0 0 1200 90" aria-hidden="true">
    <path d="M0 40 C40 30 70 26 90 26 S180 56 224 56 S320 43 358 43 S450 34 492 34 S580 60 627 60 S720 26 761 26 S850 60 895 60 S990 43 1029 43 S1120 30 1164 33 S1200 40 1200 40 L1200 90 L0 90Z" fill="#fff"/>
    <path d="M0 40 C40 30 70 26 90 26 S180 56 224 56 S320 43 358 43 S450 34 492 34 S580 60 627 60 S720 26 761 26 S850 60 895 60 S990 43 1029 43 S1120 30 1164 33 S1200 40 1200 40" fill="none" stroke="var(--orange)" stroke-width="2.5"/>
    <g fill="#fff" stroke="var(--orange)" stroke-width="2">
      <circle cx="90" cy="26" r="4"/><circle cx="224" cy="56" r="4"/><circle cx="358" cy="43" r="4"/><circle cx="492" cy="34" r="4"/><circle cx="627" cy="60" r="4"/><circle cx="761" cy="26" r="4"/><circle cx="895" cy="60" r="4"/><circle cx="1029" cy="43" r="4"/><circle cx="1164" cy="33" r="4"/>
    </g>
  </svg>
</section>

<section class="compare">
  <h2 class="section-title" style="top:754px">Find and Compare Rates</h2>
  <p class="lead" style="top:832px">Lendquay is an online marketplace where you can quickly find &amp; compare great rates from<br>leading mortgage,insurance and finance providers.</p>

  <div class="cards-bg" role="img" aria-label="Dimmed photo of a person typing on a laptop"></div>
  <svg class="abs" style="left:0;top:955px" width="1200" height="110" viewBox="0 0 1200 110" aria-hidden="true">
    <path d="M0 0H1200V48 C1050 95 150 95 0 48Z" fill="#fff"/>
    <path d="M0 48 C150 95 1050 95 1200 48" fill="none" stroke="var(--orange)" stroke-width="2.5"/>
    <circle cx="36" cy="61" r="4" fill="#fff" stroke="var(--orange)" stroke-width="2"/>
    <circle cx="1111" cy="71" r="4" fill="#fff" stroke="var(--orange)" stroke-width="2"/>
  </svg>

  <!-- row 1 -->
  <div class="card" style="left:90px;top:916px"><div class="tile" style="background:var(--plum)"><svg width="72" height="72" viewBox="0 0 72 72" fill="none" stroke="#fff" stroke-width="2.5"><rect x="10" y="8" width="44" height="56" rx="3"/><path d="M20 34L32 24 44 34V48H20Z"/><circle cx="32" cy="39" r="5"/><path d="M60 14V52L64 58 68 52V14Z"/></svg></div><div class="name one">Mortgage Rates</div></div>
  <div class="card" style="left:348px;top:916px"><div class="tile" style="background:var(--mustard)"><svg width="80" height="72" viewBox="0 0 80 72" fill="none" stroke="#fff" stroke-width="2.5"><ellipse cx="40" cy="38" rx="26" ry="18"/><path d="M14 34H8V44H16M28 54V64H36V56M48 56V64H56V54M30 20L26 10 36 18"/><circle cx="52" cy="32" r="2" fill="#fff"/></svg></div><div class="name one">Personal Finance</div></div>
  <div class="card" style="left:605px;top:916px"><div class="tile" style="background:var(--forest)"><svg width="80" height="72" viewBox="0 0 80 72" fill="none" stroke="#fff" stroke-width="2.5"><rect x="8" y="10" width="26" height="18" rx="2"/><circle cx="58" cy="18" r="10"/><path d="M58 12V24M54 15H61M55 21H62"/><path d="M10 56V44L18 34H52L62 44V56Z"/><circle cx="22" cy="58" r="5"/><circle cx="50" cy="58" r="5"/></svg></div><div class="name one">Vehicle Finance</div></div>
  <div class="card" style="left:862px;top:916px"><div class="tile" style="background:var(--mustard)"><svg width="80" height="72" viewBox="0 0 80 72" fill="none" stroke="#fff" stroke-width="2.5"><path d="M8 50H40L60 42V56L40 64H8Z"/><path d="M14 48V26L26 16 38 26V48"/><circle cx="52" cy="24" r="12"/><path d="M52 16V32M48 20H55M49 28H56"/></svg></div><div class="name one">Business &amp; Asset Finance</div></div>

  <!-- row 2 -->
  <div class="card" style="left:90px;top:1135px"><div class="tile" style="background:var(--teal)"><svg width="76" height="72" viewBox="0 0 76 72" fill="none" stroke="#fff" stroke-width="2.5"><rect x="22" y="6" width="40" height="52"/><rect x="14" y="14" width="40" height="52"/><path d="M22 30H46M22 40H46M22 50H46M38 18V28"/></svg></div><div class="name one">Commercial Finance</div></div>
  <div class="card" style="left:348px;top:1135px"><div class="tile" style="background:var(--plum)"><svg width="76" height="72" viewBox="0 0 76 72" fill="none" stroke="#fff" stroke-width="2.5"><rect x="30" y="8" width="34" height="48"/><path d="M38 20H56M38 30H56M38 40H56"/><path d="M12 52C12 42 20 36 26 36S40 42 40 52 34 64 26 64 12 62 12 52Z"/><path d="M26 44V58"/></svg></div><div class="name two">Insurance Rates</div><div class="soon">Coming Soon</div></div>
  <div class="card" style="left:605px;top:1135px"><div class="tile" style="background:var(--lilac)"><svg width="76" height="72" viewBox="0 0 76 72" fill="none" stroke="#fff" stroke-width="2.5"><circle cx="20" cy="20" r="9"/><path d="M29 20H64M56 20V26M48 20V26"/><path d="M18 58V46L24 38H50L56 46V58Z"/><circle cx="26" cy="50" r="2" fill="#fff"/><circle cx="48" cy="50" r="2" fill="#fff"/></svg></div><div class="name two">Vehicle Leasing</div><div class="soon">Coming Soon</div></div>
  <div class="card" style="left:862px;top:1135px"><div class="tile" style="background:var(--orange)"><svg width="76" height="72" viewBox="0 0 76 72" fill="none" stroke="#fff" stroke-width="2.5"><circle cx="38" cy="14" r="8"/><path d="M20 36C20 26 28 22 38 22S56 26 56 36Z"/><path d="M38 36V56"/><path d="M8 64V50L16 44 24 50V64Z"/><path d="M46 64V56L52 50H64L68 56V64Z"/></svg></div><div class="name mid">Home,Contents &amp;<br>Car Insurance</div><div class="soon">Coming Soon</div></div>

  <!-- row 3 -->
  <div class="card" style="left:90px;top:1354px"><div class="tile" style="background:var(--teal)"><svg width="72" height="72" viewBox="0 0 72 72" fill="none" stroke="#fff" stroke-width="2.5"><path d="M12 30L36 10 60 30"/><path d="M20 26V50H52V26"/><circle cx="36" cy="36" r="5"/><path d="M30 50V66H42V50"/></svg></div><div class="name mid">Farming &amp;<br>Rural Insurance</div><div class="soon">Coming Soon</div></div>
  <div class="card" style="left:348px;top:1354px"><div class="tile" style="background:var(--forest)"><svg width="72" height="72" viewBox="0 0 72 72" fill="none" stroke="#fff" stroke-width="2.5"><path d="M32 30V16C32 12 36 8 36 8S40 12 40 16V30"/><path d="M24 30H48L52 44H20Z"/><path d="M22 44L14 66M50 44L58 66M30 44L28 66M42 44L44 66"/></svg></div><div class="name two">Power &amp; Gas</div><div class="soon">Coming Soon</div></div>
  <div class="card" style="left:605px;top:1354px"><div class="tile" style="background:var(--lime)"><svg width="72" height="72" viewBox="0 0 72 72" fill="none" stroke="#fff" stroke-width="2.5"><circle cx="38" cy="38" r="26"/><ellipse cx="38" cy="38" rx="11" ry="26"/><path d="M12 38H64M16 25H60M16 51H60"/></svg></div><div class="name two">Internet &amp; Fibre</div><div class="soon">Coming Soon</div></div>
  <div class="card" style="left:862px;top:1354px"><div class="tile" style="background:var(--mustard)"><svg width="72" height="72" viewBox="0 0 72 72" fill="none" stroke="#fff" stroke-width="2.5"><rect x="22" y="6" width="30" height="60" rx="4"/><path d="M22 14H52M22 56H52"/><path d="M31 28C31 40 40 46 44 46L46 42 42 38 39 40C36 38 34 35 34 33L36 30 32 26Z"/></svg></div><div class="name two">Phone &amp; Mobile</div><div class="soon">Coming Soon</div></div>
</section>

<section class="why">
  <h2 class="section-title" style="top:1731px">Why Lendquay?</h2>
  <p class="lead" style="top:1792px">Our mission is to put the power in the hands of the consumer</p>

  <div class="why-photo" role="img" aria-label="Hands typing on a laptop at a wooden outdoor table"></div>

  <svg class="abs" style="left:90px;top:1838px" width="46" height="60" viewBox="0 0 46 60" fill="none" stroke="var(--orange)" stroke-width="2.5"><circle cx="23" cy="22" r="20"/><circle cx="23" cy="22" r="14"/><path d="M16 22L21 27 30 17"/><path d="M12 38L6 56 14 52 18 58 22 42M34 38L40 56 32 52 28 58 24 42"/></svg>
  <div class="feature" style="left:90px;top:1925px"><h3>Great Rates &amp; Incentives</h3><p>Receive the great rates and incentives hassle-free-Lendquay does the shopping around for you</p></div>

  <svg class="abs" style="left:90px;top:2069px" width="46" height="62" viewBox="0 0 46 62" fill="none" stroke="var(--orange)" stroke-width="2.5"><path d="M23 48C23 48 6 30 6 20A17 17 0 0 1 40 20C40 30 23 48 23 48Z"/><circle cx="23" cy="19" r="9"/><path d="M23 14V19L27 21"/><ellipse cx="23" cy="54" rx="14" ry="5"/></svg>
  <div class="feature" style="left:90px;top:2157px"><h3>Any Time,Any Where</h3><p>Get notifications and review representative offers wherever you are with your personal, mobile-friendly lendquay dashboard</p></div>

  <svg class="abs" style="left:1053px;top:1838px" width="58" height="58" viewBox="0 0 58 58" fill="none" stroke="var(--orange)" stroke-width="2.5"><path d="M2 20C10 8 20 4 28 4S46 8 54 20C46 32 36 36 28 36S10 32 2 20Z"/><circle cx="28" cy="20" r="9"/><circle cx="28" cy="20" r="3"/><rect x="36" y="40" width="20" height="16" rx="2"/><path d="M40 40V34A6 6 0 0 1 52 34V40"/></svg>
  <div class="feature right" style="left:820px;top:1925px"><h3>Privacy Is Important</h3><p>Your private information is disclosed<br>only when you follow up on representative<br>offers from a service provider</p></div>

  <svg class="abs" style="left:1053px;top:2069px" width="58" height="58" viewBox="0 0 58 58" fill="none" stroke="var(--orange)" stroke-width="2.5"><circle cx="29" cy="29" r="27"/><circle cx="29" cy="29" r="21"/><path d="M18 28H24V42H18Z"/><path d="M24 30L30 18C33 18 34 20 33 24L32 28H40C42 28 43 30 42 32L39 40C38 42 37 42 35 42H24"/></svg>
  <div class="feature right" style="left:770px;top:2157px;width:340px"><h3>No Fees,No Obligations</h3><p>The lendquay service is free<br>and you are under no obligation until you select<br>the representative offer that best suits your needs.</p></div>

  <div class="btn" style="left:491px;top:2284px;width:217px;height:52px">GET STARTED</div>
</section>

<footer class="site-footer">
  <div class="footer-brand">LENDQUAY</div>
  <div class="col-head" style="left:341px">LINKS</div>
  <ul class="col-list" style="left:342px"><li>Home</li><li>About Us</li><li>Careers</li><li>Media</li><li>Support</li><li>Contact Us</li></ul>
  <div class="col-head" style="left:520px">CONTACT US</div>
  <ul class="col-list" style="left:521px"><li>14 Harbour Lane,Auckland</li><li>1010,New Zealand</li><li>0508410262</li><li>info@lendquay.co.nz</li></ul>
  <div class="col-head" style="left:762px">NEWSLETTER</div>
  <div class="news-input">Enter Your Email Address</div>
  <div class="news-btn">SUBSCRIBE</div>
  <div class="copyright">Copyrights © 2020,The Company Name. All rights reserved.</div>
</footer>

</body>
</html>
```